Healthy lifestyle Influencer business card

I need your creativity to have a business card that I can leave in all the restaurants, hotels and spas I visit to inform them that I am an influencer specializing in the wellness sector and that I will write a review about them. You can use my instagram photos Lunavita27 or on my website www.piattileggeriorto.it. I would like my business card to impress with its creativity! thank you very much!

Contact Information for Business Card

siteweb, instagram, phone number

Font styles to use
Decorative
Script

Colors
0094D4
00A9DD
6FCCEA
C7EBF8
E9F6FB
59FF00
82FF00
B8FF75
E3FFCB
F4FFEA
FFC000
F8CF3A
FAE287
FDF2CF
FEFAEE
F0912C
F2A743
F7CA91
FBE8D2
FDF5EE
EE7325
F08F49
F5BC92
FAE3D3
FDF4ED
EB3D1F
EC4F4E
F09395
F8D3D4
FCEDEE
E54698
E96AAD
F1A4CE
F9D9EA
FCEFF6

Requirements
Nice to have
• creativity

```html
<!DOCTYPE html>
<html lang="it">
<head>
<meta charset="utf-8">
<title>Luna Vita Chef – Biglietto da visita</title>
<link rel="stylesheet" href="https://fonts.googleapis.com/css2?family=Great+Vibes&family=Quicksand:wght@500&family=Roboto:wght@300;400&display=swap">
<style>
  :root {
    --page-bg: #3b3b3c;
    --card-top: #1d1e20;
    --card-bottom: #2b2c2e;
    --ink-light: #f2f2f2;
    --ink-muted: #cfd1d3;
    --ink-emboss: #4a4b4e;
    --accent-teal: #8fb8ac;
    --tab-grey: #4c4d4f;
    --dot: #6fccea;
  }
  * { margin: 0; padding: 0; box-sizing: border-box; }
  html, body { width: 1200px; height: 1138px; overflow: hidden; }
  body { background: var(--page-bg); position: relative; font-family: "Roboto", sans-serif; }

  .card {
    position: absolute;
    width: 620px;
    height: 375px;
    border-radius: 18px;
    background: linear-gradient(160deg, var(--card-top) 0%, var(--card-bottom) 100%);
    overflow: hidden;
  }
  .card--front { left: 272px; top: 184px; }
  .card--back  { left: 274px; top: 606px; }

  .brand-name {
    font-family: "Quicksand", sans-serif;
    font-weight: 500;
    white-space: nowrap;
  }
  .card--front .brand-name {
    position: absolute; left: 0; right: 0; top: 128px;
    text-align: center; font-size: 50px; color: var(--ink-emboss);
  }
  .card--front .tagline {
    position: absolute; left: 0; right: 0; top: 222px;
    text-align: center; font-family: "Quicksand", sans-serif; font-size: 22px; color: var(--ink-emboss);
  }

  .social {
    position: absolute; display: flex; align-items: center; gap: 12px;
    font-size: 17px; color: var(--ink-light); font-weight: 400;
  }
  .social__dot { width: 14px; height: 14px; border-radius: 50%; background: var(--dot); }
  .card--front .social { left: 0; right: 0; top: 333px; justify-content: center; }

  .card--back .brand-name {
    position: absolute; left: 22px; top: 78px; font-size: 44px; color: var(--ink-light);
  }
  .card--back .tagline {
    position: absolute; left: 70px; top: 132px;
    font-family: "Quicksand", sans-serif; font-size: 18px; color: var(--ink-light);
  }
  .person-name {
    position: absolute; left: 22px; top: 236px;
    font-family: "Great Vibes", cursive; font-size: 32px; color: var(--ink-light);
  }
  .card--back .social { left: 22px; top: 304px; }

  .contact {
    position: absolute; left: 358px; top: 236px; list-style: none;
    font-size: 16px; font-weight: 300; color: var(--ink-muted);
  }
  .contact li { display: flex; align-items: center; gap: 12px; height: 24px; }
  .contact svg { width: 16px; height: 16px; fill: none; stroke: var(--ink-muted); stroke-width: 1.4; }

  .band-stripe {
    position: absolute; left: 0; bottom: 0; width: 330px; height: 14px; background: var(--accent-teal);
  }
  .band-tab {
    position: absolute; right: 0; bottom: 0; width: 310px; height: 46px;
    background: var(--tab-grey);
    clip-path: polygon(20px 0, 100% 0, 100% 100%, 0 100%);
  }
  .vat {
    position: absolute; left: 359px; bottom: 14px;
    font-size: 16px; font-weight: 300; color: var(--ink-muted);
  }
</style>
</head>
<body>

<section class="card card--front" aria-label="Fronte del biglietto">
  <div class="brand-name">Luna Vita Chef</div>
  <div class="tagline">Benessere in ogni piatto</div>
  <div class="social"><span class="social__dot"></span>@Lunavita27</div>
</section>

<section class="card card--back" aria-label="Retro del biglietto">
  <div class="brand-name">Luna Vita Chef</div>
  <div class="tagline">Benessere in ogni piatto</div>

  <div class="person-name">Luna Ferretti</div>
  <div class="social"><span class="social__dot"></span>@Lunavita27</div>

  <ul class="contact">
    <li>
      <svg viewBox="0 0 16 16" aria-hidden="true"><path d="M3 2h3l1.5 3.5-2 1.2a8 8 0 0 0 3.8 3.8l1.2-2L14 10v3a1 1 0 0 1-1 1A11 11 0 0 1 2 3a1 1 0 0 1 1-1z"/></svg>
      000-0000-0000
    </li>
    <li>
      <svg viewBox="0 0 16 16" aria-hidden="true"><rect x="1.5" y="3.5" width="13" height="9"/><path d="M1.5 3.5 8 9l6.5-5.5"/></svg>
      info@piattileggeriorto.it
    </li>
    <li>
      <svg viewBox="0 0 16 16" aria-hidden="true"><circle cx="8" cy="8" r="6.5"/><ellipse cx="8" cy="8" rx="3" ry="6.5"/><path d="M1.5 8h13"/></svg>
      www.piattileggeriorto.it
    </li>
  </ul>

  <div class="band-tab"></div>
  <div class="band-stripe"></div>
  <div class="vat">Partita IVA 01234560789</div>
</section>

</body>
</html>
```